Ridgeline Journeys business card

please see website
www.ridgelinejourneys.comau

info needed on card
Curtis Halvey
Ph
email
Adventure Riding GPS trails

please use my logo and colours off my site

Curtis Halvey
curtis@ridgelinejourneys.com

```html
<!DOCTYPE html>
<html lang="en">
<head>
<meta charset="utf-8">
<title>Ridgeline Journeys – Business Card</title>
<link href="https://fonts.googleapis.com/css2?family=Lato:wght@700;900&display=swap" rel="stylesheet">
<style>
  :root {
    --stage: #ecebe8;
    --card-light: #ffec2e;
    --card-deep: #ffd10f;
    --ink: #151515;
    --mark-grey: #5f5f5f;
  }
  html, body {
    margin: 0;
    width: 1200px;
    height: 900px;
    overflow: hidden;
    background: var(--stage);
    font-family: "Lato", sans-serif;
    color: var(--ink);
  }
  .canvas { position: relative; width: 1200px; height: 900px; }
  .card {
    position: absolute;
    width: 555px;
    height: 342px;
    background: linear-gradient(to top right, var(--card-light) 50%, var(--card-deep) 50%);
    box-shadow: 0 6px 18px rgba(0,0,0,0.12);
    overflow: hidden;
  }
  .card--front { left: 238px; top: 62px; }
  .card--back  { left: 458px; top: 518px; width: 559px; }

  .brand {
    position: absolute;
    display: flex;
    align-items: center;
    gap: 18px;
  }
  .brand__dot {
    border-radius: 50%;
    background: var(--mark-grey);
    flex: none;
  }
  .brand__name {
    font-weight: 900;
    text-transform: uppercase;
    line-height: 1.02;
    color: var(--ink);
  }
  .card--front .brand { left: 254px; top: 55px; }
  .card--front .brand__dot { width: 62px; height: 62px; }
  .card--front .brand__name { font-size: 25px; }

  .card--back .brand { left: 200px; top: 45px; flex-direction: row-reverse; }
  .card--back .brand__dot { width: 150px; height: 150px; }
  .card--back .brand__name { font-size: 22px; text-align: right; }

  .holder {
    position: absolute;
    left: 46px;
    top: 203px;
    margin: 0;
    font-size: 19px;
    font-weight: 700;
  }
  .contacts {
    position: absolute;
    left: 47px;
    top: 243px;
    margin: 0;
    padding: 0;
    list-style: none;
    font-size: 14.5px;
    font-weight: 700;
  }
  .contacts li {
    display: flex;
    align-items: center;
    gap: 6px;
    height: 20px;
  }
  .contacts svg { width: 12px; height: 12px; fill: var(--ink); flex: none; }

  .tagline {
    position: absolute;
    left: 36px;
    top: 278px;
    margin: 0;
    font-size: 16.5px;
    font-weight: 700;
  }
</style>
</head>
<body>
<main class="canvas">
  <section class="card card--front" aria-label="Business card front">
    <div class="brand">
      <span class="brand__dot"></span>
      <span class="brand__name">Ridgeline<br>Journeys</span>
    </div>
    <h1 class="holder">Curtis Halvey</h1>
    <ul class="contacts">
      <li>
        <svg viewBox="0 0 12 12" aria-hidden="true"><path d="M1 4c0-2 2-3 5-3s5 1 5 3l-2 1-1-1.5H4L3 5 1 4zm2 2h6l1 5H2z"/></svg>
        044-987 654 321
      </li>
      <li>
        <svg viewBox="0 0 12 12" aria-hidden="true"><path d="M1 2.5h10v7H1z M1.5 3l4.5 3.5L10.5 3" stroke="#ffec2e" stroke-width="1"/></svg>
        info@ridgelinejourneys.com
      </li>
      <li>
        <svg viewBox="0 0 12 12" aria-hidden="true"><path d="M5 7l2-2M4 5.5L2.5 7a1.8 1.8 0 0 0 2.5 2.5L6.5 8M8 6.5L9.5 5A1.8 1.8 0 0 0 7 2.5L5.5 4" fill="none" stroke="#151515" stroke-width="1.4" stroke-linecap="round"/></svg>
        www.ridgelinejourneys.comau
      </li>
    </ul>
  </section>

  <section class="card card--back" aria-label="Business card back">
    <div class="brand">
      <span class="brand__dot"></span>
      <span class="brand__name">Ridgeline<br>Journeys</span>
    </div>
    <p class="tagline">Adventure Riding GPS trails</p>
  </section>
</main>
</body>
</html>
```